Quorvane Capital LLC

Need Professional Business cards for New Investment Fund

Target Market(s)

High Quality investors

Industry/Entity Type

Financial

Contact Information for Business Card

Phone Number +1 555 284 6190
Name Lukas Varenko
Title Fund Manager
email lv@FundQuorvane.com
Website www.FundQuorvane.com

Colors

Designer to choose colors to be used in the design.

Requirements
Must have
• Must have our Logo and all of the above. Must be made so lettering and loge can be raised

```html
<!DOCTYPE html>
<html lang="en">
<head>
<meta charset="utf-8">
<title>Quorvane Capital – Business Card</title>
<link href="https://fonts.googleapis.com/css2?family=Oswald:wght@400;500;600&display=swap" rel="stylesheet">
<style>
  :root {
    --backdrop: #6a6b6d;
    --navy-deep: #080d17;
    --navy-mid: #131d35;
    --navy-blue: #1e3266;
    --ink-dark: #24242c;
    --ink-blue: #2a2f85;
    --paper: #f7f7f7;
    --brand-green: #7fe33a;
    --brand-olive: #3f4a3c;
    --text-light: #f2f2f2;
    --text-muted: #c9ccd4;
  }
  html, body {
    margin: 0;
    width: 1200px;
    height: 1200px;
    overflow: hidden;
    background: var(--backdrop);
    font-family: "Oswald", "Arial Narrow", sans-serif;
  }
  .card {
    position: absolute;
    left: 250px;
    width: 699px;
    height: 400px;
    overflow: hidden;
  }
  /* Front */
  .card-front {
    top: 147px;
    background: linear-gradient(160deg, var(--navy-mid) 0%, var(--navy-deep) 45%, var(--navy-blue) 100%);
  }
  .wave-field {
    position: absolute;
    left: 0; right: 0; bottom: 0;
    height: 190px;
    background:
      radial-gradient(ellipse 60% 40% at 45% 45%, rgba(47,79,156,.55), transparent 70%),
      radial-gradient(ellipse 50% 35% at 80% 55%, rgba(47,79,156,.4), transparent 70%),
      linear-gradient(180deg, transparent 0%, rgba(30,50,102,.6) 60%, var(--navy-blue) 100%);
  }
  .front-brand {
    position: absolute;
    top: 110px;
    left: 0; right: 0;
    text-align: center;
    font-size: 50px;
    font-weight: 500;
    letter-spacing: 4px;
    color: var(--text-light);
    text-transform: uppercase;
  }
  .front-site {
    position: absolute;
    top: 352px;
    left: 0; right: 0;
    text-align: center;
    font-size: 16px;
    letter-spacing: 1px;
    color: var(--text-muted);
  }
  /* Back */
  .card-back {
    top: 652px;
    background: var(--paper);
  }
  .back-panel {
    position: absolute;
    inset: 0;
  }
  .back-brand {
    position: absolute;
    top: 152px;
    left: 58px;
    display: flex;
    align-items: center;
    gap: 10px;
  }
  .brand-square {
    width: 22px;
    height: 22px;
    background: var(--brand-green);
  }
  .brand-name {
    font-size: 33px;
    font-weight: 500;
    letter-spacing: 2px;
    color: var(--brand-olive);
    text-transform: uppercase;
  }
  .contact {
    position: absolute;
    right: 40px;
    top: 185px;
    text-align: right;
    color: var(--text-light);
  }
  .contact-name {
    font-size: 27px;
    font-weight: 600;
    letter-spacing: 2px;
    text-transform: uppercase;
    line-height: 1.2;
  }
  .contact-title {
    font-size: 18px;
    letter-spacing: 1.5px;
    margin-top: 2px;
  }
  .contact-line {
    font-size: 19px;
    letter-spacing: 1.6px;
  }
  .contact-phone { margin-top: 30px; }
  .contact-email { margin-top: 12px; }
</style>
</head>
<body>
  <section class="card card-front">
    <div class="wave-field" role="img" aria-label="Flowing blue light waves across the lower card"></div>
    <div class="front-brand">Quorvane</div>
    <div class="front-site">www.FundQuorvane.com</div>
  </section>

  <section class="card card-back">
    <svg class="back-panel" width="699" height="400" viewBox="0 0 699 400" aria-hidden="true">
      <defs>
        <linearGradient id="panelFill" x1="0" y1="0" x2="0" y2="1">
          <stop offset="0" stop-color="#24242c"/>
          <stop offset="0.5" stop-color="#26284a"/>
          <stop offset="1" stop-color="#2a2f85"/>
        </linearGradient>
      </defs>
      <polygon points="377,0 699,0 699,400 233,400" fill="url(#panelFill)"/>
    </svg>
    <div class="back-brand">
      <span class="brand-square"></span>
      <span class="brand-name">Quorvane</span>
    </div>
    <div class="contact">
      <div class="contact-name">Lukas Varenko</div>
      <div class="contact-title">Fund Manager</div>
      <div class="contact-line contact-phone">T: +1 555 284 6190</div>
      <div class="contact-line contact-email">E: lv@FundQuorvane.com</div>
    </div>
  </section>
</body>
</html>
```